New Business Cards for Tormin Group

We need a new Business Card to compliment our new logo. We are a vibrant design, manufacture and install business providing recreation areas, public parks and Municipal spaces. We want business cards that are classy, modern and clean.

We have recently changed our logo, and are celebrating our 40th anniversary. We want business cards with a new modern design to reflect our status.

Target Market(s)

Customers

Contact Information for Business Card

We need all the details of our 3 offices as per the business card attached. Please disregard the old logo on the business card, the other three files show our new logo.

Requirements
Must have
• All info as per attached business card but with new logo.
Nice to have

```html
<!DOCTYPE html>
<html lang="en">
<head>
<meta charset="utf-8">
<title>Tormin Group Business Card</title>
<link href="https://fonts.googleapis.com/css2?family=Lato:wght@400;700&display=swap" rel="stylesheet">
<style>
  :root {
    --page-bg: #6b6b6d;
    --card-dark: #4a4a4d;
    --card-band: #5c5c5f;
    --card-light: #ffffff;
    --brand-red: #e8323a;
    --text-dark: #333335;
    --text-muted: #5a5a5c;
    --rule: #6a6a6c;
  }
  * { margin: 0; padding: 0; box-sizing: border-box; }
  html, body {
    width: 1200px; height: 1200px; overflow: hidden;
    background: var(--page-bg);
    font-family: "Lato", sans-serif;
  }
  .card {
    position: absolute; left: 240px; width: 720px; height: 420px;
    border-radius: 36px; overflow: hidden;
  }
  .card--front { top: 142px; background: var(--card-dark); }
  .card--back { top: 640px; background: var(--card-light); }

  .wordmark { display: flex; align-items: center; gap: 12px; position: absolute; }
  .wordmark__dot { border-radius: 50%; background: var(--brand-red); flex: none; }
  .wordmark__name { font-weight: 700; white-space: nowrap; }

  .card--front .wordmark { left: 50%; top: 168px; transform: translateX(-50%); }
  .card--front .wordmark__dot { width: 60px; height: 60px; }
  .card--front .wordmark__name { font-size: 50px; color: #ffffff; }

  .front-web {
    position: absolute; left: 0; right: 0; top: 374px;
    text-align: center; font-size: 13px; font-weight: 700; color: #ffffff;
  }
  .front-web .accent { color: var(--brand-red); }

  .card--back .wordmark { left: 36px; top: 80px; gap: 10px; }
  .card--back .wordmark__dot { width: 40px; height: 40px; }
  .card--back .wordmark__name { font-size: 31px; color: var(--text-dark); }

  .person { position: absolute; right: 24px; top: 90px; text-align: right; }
  .person__name { font-size: 26px; font-weight: 400; color: var(--brand-red); line-height: 1.1; }
  .person__role { font-size: 16px; color: var(--text-dark); margin-top: 8px; }
  .person__contact { margin-top: 38px; font-size: 13px; color: var(--text-dark); line-height: 28px; }

  .divider {
    position: absolute; left: 288px; right: 24px; top: 241px;
    border-top: 1.5px solid var(--rule);
  }

  .office { position: absolute; top: 256px; text-align: right; }
  .office--head { right: calc(720px - 245px); }
  .office--dubai { right: calc(720px - 478px); }
  .office--qatar { right: 24px; top: 258px; }
  .office__title { font-size: 16px; color: var(--brand-red); margin-bottom: 10px; }
  .office__line { font-size: 13px; color: var(--text-muted); line-height: 21px; white-space: nowrap; }

  .footer-shapes { position: absolute; left: 0; bottom: 0; width: 720px; height: 60px; }
  .back-web {
    position: absolute; right: 24px; top: 382px;
    font-size: 13px; color: #ffffff;
  }
</style>
</head>
<body>
  <section class="card card--front">
    <div class="wordmark">
      <span class="wordmark__dot"></span>
      <span class="wordmark__name">Tormin Group</span>
    </div>
    <p class="front-web">www.<span class="accent">tormingroup</span>.com</p>
  </section>

  <section class="card card--back">
    <div class="wordmark">
      <span class="wordmark__dot"></span>
      <span class="wordmark__name">Tormin Group</span>
    </div>

    <div class="person">
      <p class="person__name">Omar Haddani</p>
      <p class="person__role">Managing Partner</p>
      <div class="person__contact">
        <p>Phone: +971 (0)50 437 1186</p>
        <p>Email: omar@tormingroup.com</p>
      </div>
    </div>

    <div class="divider"></div>

    <div class="office office--head">
      <p class="office__title">Head Office</p>
      <p class="office__line">P.O. Box: 31842 Abu Dhabi. U.A.E</p>
      <p class="office__line">Tel No: +971 (0)2 5583120</p>
      <p class="office__line">Fax No: +971(0)2 5583121</p>
      <p class="office__line">Email: sales@tormingroup.com</p>
    </div>
    <div class="office office--dubai">
      <p class="office__title">Dubai Office</p>
      <p class="office__line">P.O. Box: 278415 Dubai, U.A.E</p>
      <p class="office__line">Tel No: +971 (0)4 327508</p>
      <p class="office__line">Fax No: +971(0)4 327509</p>
      <p class="office__line">Email: sales@tormingroup.com</p>
    </div>
    <div class="office office--qatar">
      <p class="office__title">Qater Office</p>
      <p class="office__line">P.O. Box: 20937 Doha, Qatter</p>
      <p class="office__line">Tel No: +974 44718302</p>
      <p class="office__line">Fax No: +974 44718303</p>
      <p class="office__line">Email: sales@tormingroup.com</p>
    </div>

    <svg class="footer-shapes" viewBox="0 360 720 60" aria-hidden="true">
      <rect x="0" y="395" width="260" height="25" fill="var(--card-band)"/>
      <path d="M234 420 L253 392 Q258 386 268 386 L500 386 L478 420 Z" fill="var(--card-dark)" stroke="#ffffff" stroke-width="4"/>
      <path d="M466 420 L492 381 Q497 374 507 374 L724 374 L724 424 Z" fill="var(--brand-red)" stroke="#ffffff" stroke-width="4"/>
    </svg>
    <p class="back-web">www.tormingroup.com</p>
  </section>
</body>
</html>
```